Web Design Project for SEARCH ENGINE !

We need a website design for torrents search engine.

The Website will be www.Qentrova.com

Qentrova is a a search engine for torrents.
Qentrova search and index torrents results from all torrents sites.

We will need:
Logo
WebSite Design
slogen (optional)

we need only PSDs - no codded pages are needed !

Design to the following screen Size & resolution: 1024 x 768

***PLEASE DOWNLOAD ATTACHED FILE !

```html
<!DOCTYPE html>
<html lang="en">
<head>
<meta charset="utf-8">
<title>Qentrova – torrent search</title>
<link href="https://fonts.googleapis.com/css2?family=Arimo:wght@400;700&family=Noto+Serif:wght@700&display=swap" rel="stylesheet">
<style>
:root{
  --orange:#f7941d;
  --blue:#1f8fc8;
  --text:#333;
  --muted:#999;
  --line:#d9d9d9;
  --bar:#efefef;
  --green:#2f9a2f;
  --red:#d2322d;
  --brown:#8b6a1e;
  --notice:#e6f5cf;
  --notice-line:#9dcc6a;
  --footer:#3b3b3b;
  --panel:#fafafa;
}
*{box-sizing:border-box;margin:0;padding:0}
html,body{width:683px;height:1200px;overflow:hidden}
body{font-family:"Arimo",Arial,sans-serif;font-size:10px;color:var(--text);background:#fff;position:relative}
.abs{position:absolute}
.brand{left:22px;top:30px;font:700 46px/1 "Arimo",Arial,sans-serif;color:var(--orange);letter-spacing:-1px}
.social{top:25px;width:32px;height:32px;border-radius:5px}
.tab{top:101px;height:18px;border:1px solid var(--line);border-bottom:none;background:#f3f3f3;font-size:10px;color:#555;text-align:center;line-height:17px;border-radius:3px 3px 0 0}
.tab.active{background:#fff}
.panel{left:12px;top:118px;width:658px;height:1030px;background:var(--panel);border:1px solid #e2e2e2;border-radius:3px}
.notice{left:28px;top:143px;width:623px;height:29px;background:var(--notice);border:1px solid var(--notice-line);border-radius:3px;font-size:10px;line-height:27px;padding-left:34px}
.notice i{position:absolute;left:8px;top:5px;width:17px;height:17px;border-radius:50%;background:#3b8fd1;color:#fff;font:700 11px/17px Georgia,serif;text-align:center;font-style:normal}
.bar{left:28px;width:620px;height:25px;background:var(--bar);border:1px solid var(--line);font-size:12px;line-height:23px;padding-left:10px;color:#444}
.bar small{position:absolute;right:6px;top:0;font-size:8px;color:#bbb;line-height:23px}
.src-row{left:30px;width:617px;height:20px;border-bottom:1px solid #e4e4e4;background:#fff}
.src-row.alt{background:#f4f4f4}
.src-row span{position:absolute;top:5px;font-size:9px}
.src-ico{left:2px;top:4px!important;width:10px;height:11px;background:#e5482f;border-radius:2px}
.src-site{left:17px;top:3px!important;font-size:11px!important;color:#e0562a;text-decoration:underline}
.src-title{left:180px;color:var(--blue)}
.src-cat{left:485px}
.src-age{left:562px}
.info{left:28px;top:333px;width:620px;height:37px;background:var(--notice);font-size:8px;color:#555;text-align:center;line-height:11px;padding-top:7px}
.feedback{left:28px;top:376px;width:232px;height:67px;background:#eee;border:1px solid var(--line)}
.feedback h3{font-weight:400;font-size:12px;color:#2d8fc9;padding:5px 6px;border-bottom:1px solid #ddd}
.feedback p{font-size:9.5px;padding:4px 6px 0}
.feedback b{font-weight:400;color:var(--red)}
.ad{top:376px;height:68px;border:1px solid var(--line)}
.ad-name{position:absolute;font-weight:700;font-size:18px;color:#2a5d8a}
table{border-collapse:collapse;width:100%}
.trackers{left:34px;top:486px;width:610px}
.trackers th,.related th{font:700 8.5px "Noto Serif",Georgia,serif;color:var(--brown);text-align:center;border-bottom:1px solid #ccc}
.trackers th{height:17px}
.trackers th:first-child{text-align:left}
.trackers td{font-size:9px;height:15.3px;border-bottom:1px solid #e2e2e2;text-align:center}
.trackers td:first-child{text-align:left;padding-left:3px}
.trackers td:nth-child(n+2){border-left:1px solid #e6e6e6}
.ok{color:var(--green)}.bad{color:var(--red)}.dim{color:var(--muted)}
.files{left:40px;top:618px;width:592px}
.files .root{font-weight:700;font-size:9.5px;text-decoration:underline;padding-left:18px;position:relative;height:15px}
.files .root:before{content:"";position:absolute;left:2px;top:1px;width:13px;height:9px;background:#e8b64a;border-radius:1px}
.file{height:15.5px;border-bottom:1px solid #ddd;margin-left:14px;padding-left:14px;font-size:9.5px;line-height:15px;position:relative}
.file:before{content:"";position:absolute;left:2px;top:3px;width:7px;height:9px;background:#9aa;border-radius:1px}
.file span{position:absolute;right:4px}
.related{left:34px;top:743px;width:610px}
.related th{height:16px}
.related th:first-child{text-align:left}
.related td{font-size:8.5px;height:24px;border-bottom:1px solid #e2e2e2;text-align:center;vertical-align:middle}
.related td:nth-child(n+2){border-left:1px solid #e6e6e6}
.related td:first-child{text-align:left;padding-left:16px;position:relative}
.related td:first-child:before{content:"";position:absolute;left:3px;top:6px;width:7px;height:9px;background:#aaa}
.related .name{font-weight:700;font-size:9.5px;color:#444}
.related .by{font-size:8px;color:#666}
.related .by a{color:var(--brown);text-decoration:underline}
.icons{position:absolute;right:6px;top:6px;display:flex;gap:2px}
.icons i{width:10px;height:10px;border-radius:2px;background:#c8a236}
.icons i.b{background:#2e6fb0}
.comment-title{left:36px;top:896px;font-weight:700;font-size:10px;color:var(--brown)}
.comment-box{left:35px;top:909px;width:357px;height:96px;border:1px solid #bbb;background:#fff}
.comment-box div{position:absolute;left:0;bottom:0;width:100%;height:11px;background:#8a8a8a;color:#eee;font-size:8px;line-height:11px;padding-left:8px}
.btn{left:35px;top:1008px;width:94px;height:15px;background:#b09049;color:#fff;font-size:9px;letter-spacing:.5px;text-align:center;line-height:15px}
.avatar{left:35px;top:1036px;width:34px;height:34px;background:#1f3c7a}
.post{left:80px;top:1035px;width:312px;height:70px;background:#fff;border-left:1px solid #ddd;padding:3px 0 0 4px}
.post .who{font-weight:700;color:var(--green);font-size:9px}
.post .who small{color:#666;font-weight:700;font-size:8px}
.post .score{color:var(--brown);font-size:8px;font-weight:700;margin-top:8px;padding-left:4px}
.post .body{font-size:10px;margin-top:6px;padding-left:4px}
.post .reply{display:inline-block;margin:6px 0 0 4px;background:#b09049;color:#fff;font-size:8px;padding:1px 8px}
.promo{left:447px;top:910px;width:200px;height:167px;border:1px solid #ddd;background:#fff}
.footer{left:12px;top:1146px;width:658px;height:54px;background:var(--footer);text-align:center}
.footer p{color:#fff;font-size:10px;margin-top:14px}
.footer small{display:block;color:var(--orange);font-size:7px;margin-top:9px}
</style>
</head>
<body>
<div class="abs brand">Qentrova</div>
<div class="abs social" style="left:535px;background:#4fb6d9"></div>
<div class="abs social" style="left:577px;background:#2f65b5"></div>
<div class="abs social" style="left:617px;background:#f26a21"></div>

<div class="abs tab active" style="left:408px;width:57px">Search</div>
<div class="abs tab" style="left:472px;width:53px">Qentrova</div>
<div class="abs tab" style="left:532px;width:55px">Profile</div>
<div class="abs tab" style="left:594px;width:54px">Help</div>

<div class="abs panel"></div>

<div class="abs notice"><i>i</i>Want to download Torrents anonymously? Try PeerShield, the only way to download torrents securely.</div>

<div class="abs bar" style="top:184px">Signal Drift (2011) DVDRip Vexa-TURBOCAT<small>Added 24 days ago</small></div>

<div class="abs src-row" style="top:212px"><span class="src-ico"></span><span class="src-site">grabnest.com</span><span class="src-title">Signal Drift 2011 DVDRip Vexa TURBOCAT</span><span class="src-cat">Movies</span><span class="src-age">24 days ago</span></div>
<div class="abs src-row alt" style="top:232px"><span class="src-ico"></span><span class="src-site">grabnest.com</span><span class="src-title">Signal Drift 2011 DVDRip Vexa TURBOCAT</span><span class="src-cat">Movies</span><span class="src-age">24 days ago</span></div>
<div class="abs src-row" style="top:252px"><span class="src-ico"></span><span class="src-site">grabnest.com</span><span class="src-title">Signal Drift 2011 DVDRip Vexa TURBOCAT</span><span class="src-cat">Movies</span><span class="src-age">24 days ago</span></div>
<div class="abs src-row alt" style="top:272px"><span class="src-ico"></span><span class="src-site">grabnest.com</span><span class="src-title">Signal Drift 2011 DVDRip Vexa TURBOCAT</span><span class="src-cat">Movies</span><span class="src-age">24 days ago</span></div>
<div class="abs src-row" style="top:292px"><span class="src-ico"></span><span class="src-site">grabnest.com</span><span class="src-title">Signal Drift 2011 DVDRip Vexa TURBOCAT</span><span class="src-cat">Movies</span><span class="src-age">24 days ago</span></div>
<div class="abs src-row alt" style="top:312px"><span class="src-ico"></span><span class="src-site">grabnest.com</span><span class="src-title">Signal Drift 2011 DVDRip Vexa TURBOCAT</span><span class="src-cat">Movies</span><span class="src-age">24 days ago</span></div>

<div class="abs info">To download get the P2P client here and a .torrent file from any of the torrent search engines listed above ("Download Torrent" button/link)<br>Using P2P is legal, downloading copyrighted material isn't. Be careful of what you download or face the consequences.</div>

<div class="abs feedback">
  <h3>User Feedback</h3>
  <p>Fake <b>(0)</b> | Password <b>(0)</b> | Low quality <b>(0)</b> | Virus <b>(0)</b></p>
  <p>This is verified, clean and high quality torrent <b>(33)</b></p>
</div>
<div class="abs ad" style="left:266px;width:187px;background:linear-gradient(#e9f4fb,#cfe6f5)" role="img" aria-label="Strivo 4.6 client advert with download button">
  <span class="ad-name" style="left:62px;top:14px">Strivo 4.6</span>
  <span class="abs" style="left:105px;top:37px;width:75px;height:12px;background:#3aa13a"></span>
  <span class="abs" style="left:0;bottom:0;width:100%;height:13px;background:#1e5f9a"></span>
</div>
<div class="abs ad" style="left:459px;width:187px;background:linear-gradient(#fff,#fbeede)" role="img" aria-label="Pellum browser advert, now with SwiftSeed">
  <span class="abs" style="left:8px;top:8px;width:40px;height:40px;border-radius:50%;background:#f08a24"></span>
  <span class="ad-name" style="left:62px;top:12px;color:#d83a2b;font-size:13px">Pellum browser</span>
  <span class="abs" style="left:62px;top:40px;font-size:9px;font-weight:700;color:#e07a10">now with SwiftSeed!</span>
</div>

<div class="abs bar" style="top:452px">Torrent Trackers<small>Size: 1,406 Mb</small></div>

<div class="abs trackers">
<table>
<tr><th>TRACKER NAME</th><th>STATUS</th><th>CHECKED</th><th>SEEDERS</th><th>LEECHERS</th><th>DOWNLOADS</th></tr>
<tr><td>http://relaya.net:1984/announce</td><td class="ok">active</td><td>03 August 2011, 03:20:02</td><td class="ok">3682</td><td class="bad">5783</td><td class="dim">3141</td></tr>
<tr><td>http://swarmhub.net:2710/announce</td><td class="ok">active</td><td>02 August 2011, 16:51:38</td><td class="ok">3464</td><td class="bad">7399</td><td class="dim">8021</td></tr>
<tr><td>http://secure.peerlot.net/announce</td><td class="ok">active</td><td>02 August 2011, 04:19:57</td><td class="ok">1645</td><td class="bad">5184</td><td class="dim">10</td></tr>
<tr><td>http://tracker.opentrackly.org/announce</td><td class="ok">active</td><td>01 August 2011, 10:01:05</td><td class="ok">0</td><td class="bad">0</td><td class="dim">0</td></tr>
<tr><td>http://tracker.publicswarm.org/announce</td><td class="ok">active</td><td>01 August 2011, 10:01:05</td><td class="ok">0</td><td class="bad">0</td><td class="dim">0</td></tr>
<tr><td>http://announce.seedmill.net:8080/announce</td><td class="ok">active</td><td>01 August 2011, 10:01:05</td><td class="ok">0</td><td class="bad">0</td><td class="dim">0</td></tr>
<tr><td>http://9.trackvane.net:2710/announce</td><td class="bad">private</td><td>01 August 2011, 10:31:50</td><td class="dim">-</td><td class="dim">-</td><td class="dim">-</td></tr>
</table>
</div>

<div class="abs files">
  <div class="root">Ranchers And Comets 2011 TS Vexa QuIeTrY (Size: 1.1 GB)</div>
  <div class="file">sample.avi<span>13.63 MB</span></div>
  <div class="file">ranchers--a.jpg<span>57.8 KB</span></div>
  <div class="file">rcaQuIeTrY2.avi<span>1.08 GB</span></div>
  <div class="file">QuIeTrY.nfo<span>9.07 KB</span></div>
</div>

<div class="abs bar" style="top:713px">Related Torrents<small>Size: 1,406 Mb</small></div>

<div class="abs related">
<table>
<tr><th>TORRENT NAME</th><th style="width:38px">SIZE</th><th style="width:34px">FILES</th><th style="width:35px">AGE</th><th style="width:34px">SEED</th><th style="width:38px">LEECH</th></tr>
<tr><td><div class="name">Ranchers And Comets 2011 TS Vexa QuIeTrY</div><div class="by">Posted by north_peak in <a>Movies</a></div><div class="icons"><i></i><i></i><i class="b"></i><i class="b"></i><i></i></div></td><td>1.1 GB</td><td>10</td><td>1 day</td><td class="ok">323</td><td class="bad">2299</td></tr>
<tr><td><div class="name">Ranchers And Comets 2011 TS Vexa QuIeTrY</div><div class="by">in <a>Movies</a></div><div class="icons"><i></i><i class="b"></i><i class="b"></i><i></i></div></td><td>1.1 GB</td><td>4</td><td>1 day</td><td class="ok">160</td><td class="bad">240</td></tr>
<tr><td><div class="name">Ranchers And Comets 2011 TS Vexa QuIeTrY</div><div class="by">in <a>Movies</a></div><div class="icons"><i class="b"></i><i class="b"></i><i></i></div></td><td>1.1 GB</td><td>6</td><td>1 day</td><td class="ok">0</td><td class="bad">0</td></tr>
</table>
</div>

<div class="abs bar" style="top:864px">Comments</div>

<div class="abs comment-title">Comment as a guest or sign-in</div>
<div class="abs comment-box"><div>please leave comments relating to the torrent quality or queries on the working of it only</div></div>
<div class="abs btn">POST COMMENT</div>

<div class="abs avatar" role="img" aria-label="User avatar"></div>
<div class="abs post">
  <div class="who">● KRV <small>03 Aug 2011, 08:48 (12 min. ago)</small></div>
  <div class="score">AUDIO: 8 &nbsp;&nbsp; VIDEO: 7</div>
  <div class="body">grazie.....</div>
  <span class="reply">reply</span>
</div>

<div class="abs promo" role="img" aria-label="Vestora fashion advert: coolest merchandize from the hottest brands">
  <span class="abs" style="left:0;top:0;width:100%;height:124px;background:linear-gradient(90deg,#3a2f2a,#8a6a55 60%,#c65a88)"></span>
  <span class="abs" style="left:0;top:78px;width:100%;text-align:center;color:#fff;font-weight:700;font-size:12px;line-height:14px;background:#d3367c;padding:3px 0">COOLEST MERCHANDIZE<br>FROM THE HOTTEST<br>BRANDS</span>
  <span class="abs" style="left:8px;top:140px;font-weight:700;font-size:14px;color:#d3367c">Vestora</span>
  <span class="abs" style="left:108px;top:138px;font-size:9px;color:#555;line-height:11px">WHERE FASHION<br>COMES TOGETHER</span>
</div>

<div class="abs footer">
  <p>SSL &nbsp;|&nbsp; Qentrova Plugin &nbsp;|&nbsp; Browser search plugin</p>
  <small>@ 2003-2011 Qentrova</small>
</div>
</body>
</html>
```